Telecommunications/Power civil contractor needs business card design

Were a new telecommunications/power underground civil contractor that is looking for a new business card design. Our company colours are silver or grey and orange. Feel free to use the white background logo or the black background logo.

Target Market(s)

Local contractors, utility companies, private sector mining/energy companies, developers.

Industry/Entity Type

Telecommunications

Contact Information for Business Card

Each card will need the following info:
Persons name:
Title:
E-mail:
Phone number:
Shop Address:
Mailing Address:

Requirements
Must have
• Each card will need the following info:
• Persons name:
• Title:
• E-mail:
• Phone number:
• Shop Address:
• Mailing Address:

```html
<!DOCTYPE html>
<html lang="en">
<head>
<meta charset="utf-8">
<title>Ridgeline Civil Inc – Business Card</title>
<link href="https://fonts.googleapis.com/css2?family=Montserrat:wght@400;500;700;800&display=swap" rel="stylesheet">
<style>
  :root {
    --stage: #d9d6d1;
    --card-black: #0c0c0c;
    --card-black-soft: #1e1e1e;
    --orange: #e8642c;
    --grey: #8a8a8a;
    --grey-light: #b9b9b9;
    --white: #f4f4f4;
  }
  * { box-sizing: border-box; margin: 0; padding: 0; }
  html, body {
    width: 1200px; height: 1022px; overflow: hidden;
    background: var(--stage);
    font-family: "Montserrat", Arial, sans-serif;
  }
  .stage {
    width: 1200px; height: 1022px;
    display: flex; align-items: center; justify-content: center;
  }
  .card {
    position: relative;
    width: 1000px; height: 570px;
    border-radius: 22px;
    overflow: hidden;
    background: linear-gradient(160deg, var(--card-black-soft) 0%, var(--card-black) 55%);
    box-shadow: 0 18px 40px rgba(0,0,0,0.35);
    color: var(--white);
  }
  .side-band { position: absolute; inset: 0; width: 100%; height: 100%; }
  .bottom-stripe {
    position: absolute; left: 0; right: 0; bottom: 0; height: 16px;
    background: var(--orange);
  }
  .brand {
    position: absolute; left: 64px; top: 70px;
    display: flex; align-items: center; gap: 22px;
  }
  .brand-dot {
    width: 74px; height: 74px; border-radius: 50%;
    background: var(--orange);
  }
  .brand-name {
    font-weight: 800; font-size: 44px; line-height: 1; letter-spacing: 1px;
    color: var(--grey-light); text-transform: uppercase;
  }
  .brand-name small {
    display: block; font-size: 22px; letter-spacing: 2px; margin-top: 8px;
  }
  .divider {
    position: absolute; left: 64px; top: 330px;
    width: 540px; height: 3px; background: var(--orange);
  }
  .contacts {
    position: absolute; left: 64px; top: 356px;
    list-style: none; font-size: 23px; line-height: 1.45; font-weight: 500;
  }
  .contacts li { display: flex; align-items: center; gap: 16px; }
  .contacts svg { width: 20px; height: 20px; flex: none; }
  .person {
    position: absolute; right: 170px; top: 62px;
    text-align: right;
  }
  .person-name {
    font-size: 40px; font-weight: 700; color: var(--orange);
    text-transform: uppercase; letter-spacing: 1px;
  }
  .person-title { font-size: 24px; font-weight: 500; margin-top: 6px; }
  .addresses {
    position: absolute; right: 170px; top: 182px;
    text-align: right; font-style: normal;
    font-size: 24px; line-height: 1.45; font-weight: 500;
  }
  .addresses .mail { margin-top: 10px; }
  .corner-tab {
    position: absolute; right: 36px; top: 34px;
    width: 64px; height: 46px; background: var(--white);
  }
</style>
</head>
<body>
<main class="stage">
  <section class="card" aria-label="Business card">
    <svg class="side-band" viewBox="0 0 1000 570" preserveAspectRatio="none" aria-hidden="true">
      <defs>
        <linearGradient id="bandGrey" x1="0" y1="0" x2="1" y2="1">
          <stop offset="0" stop-color="#9a9a9a"/>
          <stop offset="0.5" stop-color="#6e6e6e"/>
          <stop offset="1" stop-color="#a5a5a5"/>
        </linearGradient>
      </defs>
      <polygon points="880,0 1000,0 1000,570 790,570 880,330" fill="url(#bandGrey)"/>
    </svg>
    <div class="corner-tab"></div>

    <div class="brand">
      <span class="brand-dot"></span>
      <p class="brand-name">Ridgeline<small>Civil Inc</small></p>
    </div>

    <div class="divider"></div>

    <ul class="contacts">
      <li><svg viewBox="0 0 20 20"><rect x="5" y="2" width="10" height="16" rx="2" fill="none" stroke="#e8642c" stroke-width="2"/></svg>+330 2460-1180</li>
      <li><svg viewBox="0 0 20 20"><path d="M4 3l4 1 1 4-2 1a10 10 0 004 4l1-2 4 1 1 4-2 1C8 17 3 12 3 5z" fill="#e8642c"/></svg>+330 4259-3312</li>
      <li><svg viewBox="0 0 20 20"><rect x="2" y="4" width="16" height="12" fill="none" stroke="#e8642c" stroke-width="2"/><path d="M2 4l8 7 8-7" fill="none" stroke="#e8642c" stroke-width="2"/></svg>info@ridgelinecivil.com</li>
      <li><svg viewBox="0 0 20 20"><circle cx="10" cy="10" r="8" fill="none" stroke="#e8642c" stroke-width="2"/><path d="M2 10h16M10 2c-4 5-4 11 0 16M10 2c4 5 4 11 0 16" fill="none" stroke="#e8642c" stroke-width="1.5"/></svg>www.ridgelinecivil.com</li>
    </ul>

    <div class="person">
      <h1 class="person-name">Marcus Hale</h1>
      <p class="person-title">Director</p>
    </div>

    <address class="addresses">
      <p class="shop">48 Quarry Lane<br>Millbrook, NY 12545</p>
      <p class="mail">PO BOX 3051<br>RESEDA, CA 91335</p>
    </address>

    <div class="bottom-stripe"></div>
  </section>
</main>
</body>
</html>
```